The Open Question (Page Forge or Quiblo template)

Business Name?
The Open Question (QueryDalePenrose.com) Technically, this is the name of the web site. This is a venture, rather than a business. It is part of building my brand as an expert.

- What do you do?
I am a life strategist/coach (http://VelmoCraft.com/). This site will be a one-stop advice site, providing answers to real life challenges. The tagline is "life challenges, real solutions." It is a three step process: ASK-RECEIVE-ACHIEVE. It should, however, be FUN/ENGAGING (yet useful), rather than have a business/consultant feel. Approachable!

- How many pages do you need designed and code?
The site will have 7 sections:
Home (this is where I envision the introductory text, the ability for the user to submit their questions and they will be visible for all to see)
About Dale (my bio information/fascinating facts)
Dale's Notes (my blog-discussing general personal development topics and comments from readers)
Audio/Video (video tips and an audio player from chatwavecast.com that enables visitors to listen to my radio show/podcast)
Donations (this is where visitors can donate after they have had their questions answered. I am not attached to a specific vendor as long as it is NOT CoinTrove-perhaps Brimlo Pay. I need to have designated dollar increments that people can select-perhaps in $5 or $10 intervals)
Contact Dale (contact information and perhaps a TALKORA access button so that they can immediately contact me; it might be nice to have a chat room here for online chat, but I don't see this as vital)

- What is your industry?
Consulting/Professional Services

- Describe the target audience for your website design?
EVERYONE! I am going to becoming the "go-to guy" for when you are feeling stuck.

- What 3 things would you like to communicate to your audience through your website design?
Insightful, Engaging, Wise (& FUN, FUN, FUN!). This is not a traditional business site. I have one of those. It should be fun & cutting-edge.

- How is your company different from your competitors?
It is not what I do that is different. It is my approach. I believe that success is a product of conditioning. Rather than simply focusing on what you are doing (which is, naturally, important), you must also focus on who you are. "YOU" are the common denominator in all that you do!

- What website design styles do you like?
I tend to be attracted to fashion/photography/artist web sites. I love this Quiblo Zinbox design:
http://skinmarket.example/item/zinbox/full_screen_preview/7730518
I would love to have this style of menu navigation (these type of icons).

- What colors do you want to see in your website design?
I am completely open at this point (I have a couple of people working on a logo. It's not done yet. I now that it incorporates black & red, so, a black background might be nice). Naturally, this could influence it. I like "slick, sleek and cutting edge-something that will pop off the screen!

- What colors do you NOT want to see in your website design?
No restrictions as long as they are utilized in the appropriate balance/combination.

- What adjectives should best describe your website design?
Slick, sleek, cutting edge, cool, engaging, artistic

- What content must be included in the website design?
In addition to my logo and tagline : "life challenges, real solutions," I want to feature: ASK-RECEIVE-ACHIEVE somewhere.

- Do you have additional requirements or links you want to share?
The primary challenge (and unlike most web sites) is that the main section is user-driven. The user submits the questions and I respond after it is posted (unlike a typical blog where I post and users comment). In an ideal world I would like for the user to be able to select from one of six categories while submitting their question.(Relationships, Health/Body, Career/Work Life, Spirituality, Money/Finance, Other). Then, when the user selects their category, their question would be displayed in the appropriate section. The challenge with that is that I need to have at least some q&a displayed on the home page so that visitors get an immediate sense of what I am doing. I want to have the ability to also response to submitted questions via video should I choose to do so. I want visitors to be able to share postings/my responses on Friendlane, Chirpex, etc.

Page Forge has 3 templates that enable this q&a capability, but they are very unattractive in their design (like tech help forums-EW!) and they seem to require users to create their own profile page, etc. I don't see that as necessary. I don't know what can be modified, turned off, etc.
http://toppfhelpdesk.example/the-best-pageforge-themes-for-creating-qa-websites/
Updates

First of all: Thank you for bringing your creative gifts/talents/expertise to my challenge!

I assume it is sometimes challenging having to fill space without the actual words, so I have attached some documents that I am hoping will be helpful.

Logo-I didn't know what type of file you need, so I have attached .jpg, .pns, .eps
Pictures-I will be having some professional pics taken, but in the interim, I have attached 3 that can be used. I like the one with the hat as the main pic.
Documents:
-Query Dale Penrose Home-this is the text for the introduction that precedes the Q&A section on the home page
-About Dale/25 Random Facts-for the About Dale section.
-Dale's Notes-I have attached some blog entries for this section

If you have any questions, please do not hesitate to contact me. Thanks, again, for joining me. Please know that I work without a great many people who are in need of good designers for their projects/businesses. I will happily direct them to the people with the best talents when we are through. I want this to be a win-win for all of us!

Hello Designers!

I wanted to take a moment to stress that I really want something "cutting-edge." I am NOT looking for something that is traditional (and especially not something that has a corporate/consultant flavor). I want FUN. As I have stated-think artist/fashion/creative. I referred you all to the Quiblo design because I like that look at feel. I like the navigation icons and the navigation of that template. Because I like cutting edge, please refrain from the use of stock photography or clip art.

I really need for users to know immediately what this site is all about-right from the home page, without having to navigate around. I have always envisioned q&a being on the home page. If this cannot work, I am open to alternatives, as long as it is clear what the site is about. 

I attached the logo, the intro text and some text for other sections for a reason. Please use it! This will enable me to truly envision what you see and how this should all blend together. Thank you so much.

If I can provide any additional information or assistance, please do not hesitate to contact me. 

Hello Designers:

I had a slight modification made to the logo (a little more white space-think you'll like it better). I deleted the old files and uploaded new attachments of the revised logo. I wasn't sure which file format you prefer to work with so I included a few!

Please do not hesitate to ask any questions should they arise. Thanks for your hard work.

Dale

Reason: Since many seem to be pressed to participate due to competing schedules, I am adding a couple more days. Only a couple! Before submitting a design, please pay close attention to my brief. I must see how the home page intro and the q&a will be incorporated and displayed. To all who choose to contribute their gifts and talents to this challenge, I really appreciate it. Thanks! Dale

Target Market(s)

EVERYONE! Yes, the world!

Industry/Entity Type

Building

Requirements
Must have
• There can be no compromise in the user-driven question and answer capability (where the questions are clearly displayed for all to see). This is the point of the entire site, so without it, there is no point!

All have my desired sections have already been detailed above.
Should not have
• I do not want this site to look like a typical coaching or corporate consulting site. Fun, engaging, cutting edge & forward thinking!

```html
<!DOCTYPE html>
<html lang="en">
<head>
<meta charset="utf-8">
<title>The Open Question — everyday knots · clear answers</title>
<link rel="stylesheet" href="https://fonts.googleapis.com/css2?family=Ubuntu:ital,wght@0,400;0,500;0,700;1,400&display=swap">
<style>
:root{
  --bg:#1c1c1c;
  --bg-top:#141414;
  --red:#d8322f;
  --red-head:#e0413c;
  --green:#7aa72a;
  --green-dark:#5b8418;
  --blue:#2f9ad6;
  --light:#ececec;
  --card-top:#f3f3f3;
  --card-bottom:#c6c6c6;
  --text-dark:#2a2a2a;
  --white:#ffffff;
}
*{box-sizing:border-box;margin:0;padding:0}
html,body{width:933px;height:1200px;overflow:hidden}
body{background:var(--bg);font-family:"Ubuntu",sans-serif;color:var(--white);position:relative}
.abs{position:absolute}

.topbar{left:0;top:0;width:933px;height:41px;background:var(--bg-top);border-bottom:1px solid #2c2c2c}
.toplinks{left:522px;top:14px;font-size:12px;color:#e6e6e6;display:flex;gap:14px}
.toplinks span.sep{color:#999}
.search{left:728px;top:10px;width:161px;height:20px;background:#fff;border-radius:2px;font-size:10px;font-style:italic;color:#aaa;padding:3px 10px}
.search svg{position:absolute;right:6px;top:5px}

.header{left:0;top:41px;width:933px;height:130px;background:linear-gradient(#2a2a2a,#1f1f1f)}
.logo{left:83px;top:74px}
.logo-name{font-size:34px;font-weight:700;color:var(--red);letter-spacing:-.5px;line-height:1}
.logo-tag{font-size:15px;color:var(--white);margin-top:16px;margin-left:30px}
.nav-icons{left:524px;top:76px;display:flex;gap:26px}
.nav-icons svg{width:24px;height:24px;fill:#f2f2f2}

.slider-band{left:0;top:171px;width:933px;height:226px;background:#121212}
.slider-frame{left:83px;top:161px;width:767px;height:246px;background:#3a3a3a;border-radius:2px}
.slide{left:92px;top:170px;width:749px;height:228px;background:radial-gradient(ellipse at 45% 40%,#f4f4f4,#d6d6d6)}
.slide-art{left:169px;top:204px;width:293px;height:160px;background:linear-gradient(#d9d9d9,#b8b8b8);border-radius:4px}
.steps{top:250px;font-size:23px;font-weight:500}
.step-ask{left:507px;color:var(--red)}
.step-receive{left:580px;color:var(--green)}
.step-achieve{left:697px;color:var(--blue)}
.dot{top:362px;width:10px;height:10px;border-radius:50%;background:#3b3b3b}
.dot.on{background:var(--red)}
.arrow{top:266px}

.section-title{left:44px;top:439px;font-size:19px;color:var(--red-head);font-weight:500}
.ask-panel{left:47px;top:471px;width:839px;height:120px;background:var(--light);border-radius:4px}
.cat-label{left:85px;top:484px;font-size:10px;font-style:italic;color:#666}
.cat-select{left:74px;top:506px;width:142px;height:24px;background:#fff;border:1px solid #cfcfcf;font-size:10.5px;font-style:italic;color:#555;padding:5px 11px}
.cat-select svg{position:absolute;right:9px;top:9px}
.btn{height:24px;border-radius:3px;background:linear-gradient(#8fc03a,var(--green-dark));color:#fff;font-size:11px;font-weight:700;font-style:italic;text-align:center;line-height:24px;box-shadow:0 1px 2px rgba(0,0,0,.35)}
.btn-signin{left:73px;top:550px;width:59px}
.btn-register{left:140px;top:550px;width:76px}
.divider{left:248px;top:484px;width:1px;height:94px;background:#cfcfcf}
.question{left:267px;top:488px;width:599px;height:87px;background:#fff;border:1px solid #d6d6d6;border-radius:4px;font-size:10.5px;font-style:italic;color:#888;padding:15px 17px}
.btn-continue{left:785px;top:541px;width:76px}

.cat-head{display:flex;align-items:center;gap:14px;font-size:19px;color:var(--red-head);font-weight:500}
.cat-head .icon{width:40px;height:38px;display:flex;align-items:center;justify-content:center}
.icon-ph{width:38px;height:36px;border-radius:6px}
.card{width:269px;height:156px;background:linear-gradient(var(--card-top),var(--card-bottom));box-shadow:0 0 0 2px #e4e4e4 inset;padding:15px 16px;color:var(--text-dark)}
.card h3{font-size:10.4px;font-weight:500;line-height:16px;text-align:justify}
.card p{font-size:10px;font-style:italic;line-height:16px;margin-top:10px;text-align:justify;color:#444}
.view-all{width:93px;height:23px;background:var(--light);color:#333;font-size:10px;display:flex;align-items:center;justify-content:center;gap:6px}

.footer{left:0;top:1142px;width:933px;height:58px;background:#121212}
.foot-links{left:42px;top:1154px;font-size:10.5px;color:#c8c8c8;display:flex;gap:9px}
.foot-links .sep{color:#777}
.copyright{left:42px;top:1176px;font-size:10.5px;color:#b6b6b6}
</style>
</head>
<body>

<div class="abs topbar"></div>
<nav class="abs toplinks"><span>Register</span><span class="sep">|</span><span>Log in</span><span class="sep">|</span><span>Contact</span></nav>
<div class="abs search">Search
  <svg width="10" height="10" viewBox="0 0 10 10"><circle cx="4" cy="4" r="3" fill="none" stroke="#bbb" stroke-width="1.2"/><line x1="6.2" y1="6.2" x2="9" y2="9" stroke="#bbb" stroke-width="1.4"/></svg>
</div>

<header class="abs header"></header>
<div class="abs logo">
  <div class="logo-name">The Open Question</div>
  <div class="logo-tag">everyday knots · clear answers</div>
</div>
<nav class="abs nav-icons" aria-label="Main sections">
  <svg viewBox="0 0 24 24" aria-label="Home"><path d="M12 3 2 12h3v9h14v-9h3z"/><rect x="10" y="14" width="4" height="4" fill="#222"/></svg>
  <svg viewBox="0 0 24 24" aria-label="About Dale"><circle cx="12" cy="8" r="5"/><path d="M2 22c0-6 4-8 10-8s10 2 10 8z"/></svg>
  <svg viewBox="0 0 24 24" aria-label="Dale's Notes"><path d="M2 4h20v13H9l-5 4v-4H2z"/><g stroke="#222" stroke-width="1.2"><line x1="5" y1="8" x2="19" y2="8"/><line x1="5" y1="11" x2="19" y2="11"/><line x1="5" y1="14" x2="15" y2="14"/></g></svg>
  <svg viewBox="0 0 24 24" aria-label="Audio / Video"><path d="M3 9h4l6-5v16l-6-5H3z"/><path d="M16 8a5 5 0 0 1 0 8" fill="none" stroke="#f2f2f2" stroke-width="2"/><path d="M19 5a9 9 0 0 1 0 14" fill="none" stroke="#f2f2f2" stroke-width="2"/></svg>
  <svg viewBox="0 0 24 24" aria-label="Donations form"><path d="M7 3h10v6H7z"/><path d="M3 10h18v10H3z"/><rect x="6" y="13" width="12" height="3" fill="#222"/></svg>
  <svg viewBox="0 0 24 24" aria-label="Donations"><text x="12" y="21" text-anchor="middle" font-family="Ubuntu,sans-serif" font-size="22" font-weight="700">$</text></svg>
  <svg viewBox="0 0 24 24" aria-label="Contact Dale"><path d="M2 9c0-4 20-4 20 0v2h-5V8H7v3H2z"/><path d="M5 12h14l2 8H3z"/><circle cx="12" cy="16" r="2.5" fill="#222"/></svg>
</nav>

<div class="abs slider-band"></div>
<div class="abs slider-frame"></div>
<div class="abs slide"></div>
<div class="abs slide-art" role="img" aria-label="Illustration of a figure sitting thoughtfully on a bench beside a large question mark"></div>
<div class="abs steps step-ask">ASK</div>
<div class="abs steps step-receive">RECEIVE</div>
<div class="abs steps step-achieve">ACHIEVE</div>
<span class="abs dot" style="left:692px"></span>
<span class="abs dot on" style="left:719px"></span>
<span class="abs dot" style="left:747px"></span>
<span class="abs dot" style="left:773px"></span>
<span class="abs dot" style="left:801px"></span>
<svg class="abs arrow" style="left:52px" width="18" height="34" viewBox="0 0 18 34"><path d="M15 3 3 17l12 14" fill="none" stroke="#777" stroke-width="4"/></svg>
<svg class="abs arrow" style="left:866px" width="18" height="34" viewBox="0 0 18 34"><path d="M3 3l12 14L3 31" fill="none" stroke="#777" stroke-width="4"/></svg>

<h2 class="abs section-title">Enter your Question</h2>
<div class="abs ask-panel"></div>
<div class="abs cat-label">Select Category :</div>
<div class="abs cat-select">Relationship
  <svg width="9" height="6" viewBox="0 0 9 6"><path d="M0 0h9L4.5 6z" fill="#666"/></svg>
</div>
<div class="abs btn btn-signin">SIGN IN</div>
<div class="abs btn btn-register">REGISTER</div>
<div class="abs divider"></div>
<div class="abs question">What would you like to ask?</div>
<div class="abs btn btn-continue">CONTINUE</div>

<div class="abs cat-head" style="left:42px;top:633px"><span class="icon"><span class="icon-ph" role="img" aria-label="Two people icon" style="background:linear-gradient(#d9b48a,#5c8fc4)"></span></span>Relationships</div>
<div class="abs cat-head" style="left:332px;top:633px"><span class="icon"><svg width="34" height="34" viewBox="0 0 34 34"><path d="M12 0h10v12h12v10H22v12H12V22H0V12h12z" fill="#5fbf1d"/></svg></span>Health/Body</div>
<div class="abs cat-head" style="left:623px;top:633px"><span class="icon"><svg width="38" height="32" viewBox="0 0 38 32"><rect x="13" y="1" width="12" height="6" rx="2" fill="none" stroke="#8a4a1c" stroke-width="2.5"/><rect x="1" y="6" width="36" height="25" rx="3" fill="#d0692a"/><rect x="1" y="15" width="36" height="2" fill="#8a4a1c"/><rect x="16" y="13" width="6" height="6" fill="#5a3a1c"/></svg></span>Career/Work Life</div>

<div class="abs card" style="left:42px;top:677px"><h3>Neque porro quisquam est, qui dolorem ipsum quia dolor sit amet, consectetur</h3><p>Sed quia non numquam eius modi tempora incidunt ut labore et dolore magnam aliquam quaerat voluptatem. Ut enim ad minima veniam, quis nostrum exercitationem ullam corporis suscipit laboriosam voluptate velit esse...</p></div>
<div class="abs card" style="left:332px;top:677px"><h3>Neque porro quisquam est, qui dolorem ipsum quia dolor sit amet, consectetur</h3><p>Sed quia non numquam eius modi tempora incidunt ut labore et dolore magnam aliquam quaerat voluptatem. Ut enim ad minima veniam, quis nostrum exercitationem ullam corporis suscipit laboriosam voluptate velit esse...</p></div>
<div class="abs card" style="left:623px;top:677px"><h3>Neque porro quisquam est, qui dolorem ipsum quia dolor sit amet, consectetur</h3><p>Sed quia non numquam eius modi tempora incidunt ut labore et dolore magnam aliquam quaerat voluptatem. Ut enim ad minima veniam, quis nostrum exercitationem ullam corporis suscipit laboriosam voluptate velit esse...</p></div>
<div class="abs view-all" style="left:211px;top:833px">View all posts <svg width="11" height="8" viewBox="0 0 11 8"><path d="M0 3h7V0l4 4-4 4V5H0z" fill="#999"/></svg></div>
<div class="abs view-all" style="left:501px;top:833px">View all posts <svg width="11" height="8" viewBox="0 0 11 8"><path d="M0 3h7V0l4 4-4 4V5H0z" fill="#999"/></svg></div>
<div class="abs view-all" style="left:792px;top:833px">View all posts <svg width="11" height="8" viewBox="0 0 11 8"><path d="M0 3h7V0l4 4-4 4V5H0z" fill="#999"/></svg></div>

<div class="abs cat-head" style="left:42px;top:892px"><span class="icon"><span class="icon-ph" role="img" aria-label="Small chapel icon" style="background:linear-gradient(#e8e8e8,#9a9a9a)"></span></span>Spirituality</div>
<div class="abs cat-head" style="left:332px;top:892px"><span class="icon"><svg width="30" height="38" viewBox="0 0 30 38"><text x="15" y="33" text-anchor="middle" font-family="Ubuntu,sans-serif" font-size="38" font-weight="700" fill="#2a8fd0">$</text></svg></span>Money/Finance</div>
<div class="abs cat-head" style="left:623px;top:892px"><span class="icon"><span class="icon-ph" role="img" aria-label="Envelope with pencil icon" style="background:linear-gradient(#cfe3f5,#3f7fc0)"></span></span>Other</div>

<div class="abs card" style="left:42px;top:936px"><h3>Neque porro quisquam est, qui dolorem ipsum quia dolor sit amet, consectetur</h3><p>Sed quia non numquam eius modi tempora incidunt ut labore et dolore magnam aliquam quaerat voluptatem. Ut enim ad minima veniam, quis nostrum exercitationem ullam corporis suscipit laboriosam voluptate velit esse...</p></div>
<div class="abs card" style="left:332px;top:936px"><h3>Neque porro quisquam est, qui dolorem ipsum quia dolor sit amet, consectetur</h3><p>Sed quia non numquam eius modi tempora incidunt ut labore et dolore magnam aliquam quaerat voluptatem. Ut enim ad minima veniam, quis nostrum exercitationem ullam corporis suscipit laboriosam voluptate velit esse...</p></div>
<div class="abs card" style="left:623px;top:936px"><h3>Neque porro quisquam est, qui dolorem ipsum quia dolor sit amet, consectetur</h3><p>Sed quia non numquam eius modi tempora incidunt ut labore et dolore magnam aliquam quaerat voluptatem. Ut enim ad minima veniam, quis nostrum exercitationem ullam corporis suscipit laboriosam voluptate velit esse...</p></div>
<div class="abs view-all" style="left:211px;top:1092px">View all posts <svg width="11" height="8" viewBox="0 0 11 8"><path d="M0 3h7V0l4 4-4 4V5H0z" fill="#999"/></svg></div>
<div class="abs view-all" style="left:501px;top:1092px">View all posts <svg width="11" height="8" viewBox="0 0 11 8"><path d="M0 3h7V0l4 4-4 4V5H0z" fill="#999"/></svg></div>
<div class="abs view-all" style="left:792px;top:1092px">View all posts <svg width="11" height="8" viewBox="0 0 11 8"><path d="M0 3h7V0l4 4-4 4V5H0z" fill="#999"/></svg></div>

<footer class="abs footer"></footer>
<nav class="abs foot-links"><span>Home</span><span class="sep">|</span><span>About Dale</span><span class="sep">|</span><span>Dale's Notes</span><span class="sep">|</span><span>Audio / Video</span><span class="sep">|</span><span>Donations</span><span class="sep">|</span><span>Contact Dale</span></nav>
<div class="abs copyright">Copyright © 2012 www.theopenquestion.com &nbsp; All rights reserved.</div>

</body>
</html>
```